Wordpress Theme for Medical Clinics

** Please view updated Sitemap2.pdf doc to clarify some confusion ***

This is a multiuser WordPress subscription site for medical clinics. Please see attachment for sitemap. Please do not include extra content like social media icons, search bars, or images. If you have questions, please ask for clarification.
The site contains the following pages and sub-pages:

1. Home
2. Our Clinic
2a. Our Clinic > Mission
2b. Our Clinic > Services
2c. Our Clinic > Clinic Policies
2d. Our Clinic > Schedules
3. Our Staff
3a. Our Staff > [Staff member page]
4. Resources
4a. Resources > Patient Health (index)
4b. Resources > Patient Health (index) > [post]
4c. Resources > Links
4d. Resources > Forms
5. Alerts
5a. Alerts > [Alert Page]
6. Contact Us

Includes the Following Pages, Subpages, and Content
1. Home
a. About Us
b. Our Staff
c. Bulletins
d. Accepting New Patients (shown as an alert widget)
e. Links
i. Physician Toolbox
ii. Book an Appointment
f. Clinic Policies
i. Show first 3 policies (e.g. Late Arrivals, Missed Appointments, Fees)
ii. Link to Clinic Policies page
g. Primary widget (displayed on all pages)
i. Hours of operation
ii. Contact Info
1. Tel
2. Fax
3. Email
4. Address
5. Get directions (link to Google Maps)
2. Our Clinic
a. Main Page
i. Clinic Name
ii. Overview
iii. Languages Spoken
iv. Secondary Navigation
1. Mission
2. Services
3. Clinic Policies
4. Schedules (see attachment)
b. Our Clinic > Mission
c. Our Clinic > Services
i. For each service include service TITLE and DESCRIPTION
d. Our Clinic > Clinic Policies
i. For each policy include policy TITLE and DESCRIPTION
ii. Include the following policies in mockup
1. Late arrivals
2. Missed appointments
3. Fees for missed appointments
4. Referrals and follow-ups
5. Services not covered by RDA
6. Information for LTF patients
7. Medical Legal Reports
e. Our Clinic > Schedules
3. Our Staff
a. Main Page
i. Display a list of staff members. Include NAME and DESIGNATION
b. Our Staff > [Staff Name]
i. Include NAME, PICTURE, DESIGNATION, and BIO
4. Resources
a. Resources > Patient Health
i. Main Page
1. Posts (ordered by date)
a. Title
b. Summary
2. Side Navigation
a. Post Categories
ii. Patient Health > [post title]
1. Title
2. Post Category
3. Date
4. Author
5. Summary
6. Body
b. Resources > Links
1. Secondary Navigation - Categories
a. Sample Categories:
i. Local Services
ii. RDA and Drug Coverage
iii. Mental Health Resources
2. Category page
a. Include the following links in the 'Local Services' category
i. Hypertension clinics
ii. Home Care services
iii. Vaccine Clinics
c. Resources > Forms
i. Display a table with form TITLE and CATEGORY
ii. Side Navigation
1. Form Categories
a. Use the following sample Categories
i. Referrals
ii. Insurance
iii. Intake
iv. Discharge
v. Waivers
5. Alerts
a. Main page
i. List of all Alert posts
1. Include post TITLE as a link to the post
ii. Side Navigation
1. Alerts Archive
a. shown as Month + Number of posts
iii. Alerts > [Alert page]
1. Include TITLE, DATE, AUTHOR, BODY
6. Contact Us
a. Map
b. Hours of operation
c. Address
d. Phone number
e. Fax number
e. Fax number
f. Map
g. Email

Design notes:
- fixed width
- responsive (need designs for mobile, tablet, and desktop)
- simple, dark font, white background
- use Font Awesome icons where needed
- user adds own logo

Target Market(s)

Medical Clinics

Industry/Entity Type

Medical

Number of Pages Required

5+ page

Font styles to use
Serif
Sans Serif

Requirements
Must have
• Please keep designs very simple.
• Examples:
• https://www.quolbin.com/install
• http://www.ventrohax.com/company/about-us
• http://brindlequota.org/
• http://www.trosk.com/
Should not have
• Minimal or no use of shadows and gradients

```html
<!DOCTYPE html>
<html lang="en">
<head>
<meta charset="utf-8">
<title>Medical Clinics – Resources Links</title>
<link href="https://fonts.googleapis.com/css2?family=Open+Sans:wght@400;600;700&family=Raleway:wght@500;600;700&display=swap" rel="stylesheet">
<style>
:root{
  --blue:#0a8be0;
  --ink:#2b2b2b;
  --band:#f7f7f7;
  --rule:#d9d9d9;
  --footer:#232323;
  --footer-text:#8a8a8a;
  --white:#fff;
}
*{margin:0;padding:0;box-sizing:border-box}
html,body{width:1200px;height:866px;overflow:hidden}
body{position:relative;background:var(--white);font-family:"Open Sans",Arial,sans-serif;color:var(--ink);font-size:10px}
a{color:inherit;text-decoration:none}
ul{list-style:none}

.topbar{position:absolute;top:0;left:0;width:1200px;height:30px;background:var(--blue);color:var(--white);font-size:9.5px}
.topbar .help{position:absolute;left:161px;top:8px}
.topbar .sep{display:inline-block;width:1px;height:14px;background:var(--white);vertical-align:middle;margin:0 5px}
.topbar .tools{position:absolute;right:161px;top:8px}

.header{position:absolute;top:30px;left:0;width:1200px;height:83px}
.brand{position:absolute;left:162px;top:25px;display:flex;align-items:center;gap:16px;font-family:"Raleway",Arial,sans-serif;font-weight:600;font-size:21px;color:var(--ink)}
.brand .dot{width:30px;height:30px;border-radius:50%;background:var(--blue)}
.main-nav{position:absolute;top:0;right:0;height:83px;font-size:10.5px}
.main-nav li{position:absolute;top:0}
.main-nav a{display:block;height:83px;line-height:83px;color:var(--ink)}
.main-nav .active a{background:var(--blue);color:var(--white);width:60px;text-align:center}

.page-title{position:absolute;top:113px;left:0;width:1200px;height:59px;background:var(--band)}
.page-title h1{position:absolute;left:162px;top:15px;font-size:10px;font-weight:700;text-transform:uppercase}
.page-title .crumbs{position:absolute;left:162px;top:34px;font-size:9.5px}

.side-nav{position:absolute;left:162px;top:218px;width:202px}
.side-nav h2,.content h2{font-size:10.5px;font-weight:700;text-transform:uppercase;padding-bottom:5px;border-bottom:1px solid var(--rule)}
.side-nav ul{margin-top:18px;border-left:3px solid #e2e2e2;padding-left:11px}
.side-nav li{height:22.5px;line-height:13px;font-size:9.5px}
.side-nav li.current{color:var(--blue);font-weight:700}

.content{position:absolute;left:387px;top:216px;width:426px}
.content h2{font-size:12.5px;font-weight:600}
.link-list{margin-top:14px;padding-left:10px}
.link-list li{height:18px;font-size:10px;color:var(--blue);display:flex;align-items:center;gap:7px}
.link-list svg{flex:none}

.info-card{position:absolute;left:836px;top:210px;width:203px;height:361px;border:1px solid var(--rule);border-radius:2px}
.info-card h3{background:var(--blue);color:var(--white);font-size:10.5px;font-weight:700;height:33px;line-height:33px;padding-left:13px;text-transform:uppercase}
.info-card .intro{padding:8px 22px 0 14px;font-size:9.5px;line-height:14px}
.hours{margin:8px 14px 0;font-size:9.5px}
.hours div{display:flex;height:18px}
.hours dt{width:90px}
.rule{margin:26px 14px 0;border-top:1px solid var(--rule)}
.info-card h4{margin:18px 14px 0;font-size:10.5px;font-weight:700}
.contact{margin:7px 14px 0;font-size:9.5px}
.contact div{display:flex}
.contact dt{width:93px}
.contact dd{line-height:15px}

.footer{position:absolute;left:0;top:638px;width:1200px;height:228px;background:var(--footer);border-top:4px solid var(--blue);color:var(--footer-text)}
.footer .brand{position:absolute;left:161px;top:38px;color:var(--white);font-size:20px}
.footer .about{position:absolute;left:162px;top:87px;width:205px;font-size:9px;line-height:13.5px;color:#cfcfcf}
.footer-col{position:absolute;top:35px}
.footer-col h5{font-family:"Raleway",Arial,sans-serif;font-size:12.5px;font-weight:700;color:#9a9a9a;margin-bottom:7px}
.footer-col li{height:18px;font-size:9.5px}
.footer-col li.on{color:#e5e5e5}
.footer-contact{font-size:9.5px;margin-left:2px}
.footer-contact div{display:flex;line-height:15px}
.footer-contact dt{width:88px}
.footer .bottom{position:absolute;left:0;top:188px;width:1200px;border-top:1px solid #3a3a3a;font-size:9.5px}
.footer .bottom span{position:absolute;top:9px}
</style>
</head>
<body>

<div class="topbar">
  <div class="help">To help Here : 000 555 0142<span class="sep"></span>Email : Contact@ Velmora.ca</div>
  <div class="tools"><a href="#">Book an Appointment</a><span class="sep"></span><a href="#">Physician Toolbox</a></div>
</div>

<header class="header">
  <a class="brand" href="#"><span class="dot"></span>Medical Clinics</a>
  <ul class="main-nav">
    <li style="left:-629px"><a href="#">Home</a></li>
    <li style="left:-561px"><a href="#">Our Clinic</a></li>
    <li style="left:-474px"><a href="#">Our Staff</a></li>
    <li class="active" style="left:-397px"><a href="#">Resources</a></li>
    <li style="left:-303px"><a href="#">Alerts</a></li>
    <li style="left:-236px"><a href="#">Contact Us</a></li>
  </ul>
</header>

<section class="page-title">
  <h1>Resources Links</h1>
  <div class="crumbs">HOME / RESOURCES/LINKS</div>
</section>

<aside class="side-nav">
  <h2>Resources Links</h2>
  <ul>
    <li class="current">Local Services</li>
    <li>RDA and Drug Coverage</li>
    <li>Mental Health Resources</li>
  </ul>
</aside>

<main class="content">
  <h2>Local Services</h2>
  <ul class="link-list">
    <li><svg width="5" height="7" viewBox="0 0 5 7"><path d="M1 1l2.5 2.5L1 6" fill="none" stroke="#2b2b2b" stroke-width="1.2"/></svg><a href="#">Lorem Ipsum is simply dummy text of the printing.</a></li>
    <li><svg width="5" height="7" viewBox="0 0 5 7"><path d="M1 1l2.5 2.5L1 6" fill="none" stroke="#2b2b2b" stroke-width="1.2"/></svg><a href="#">Typesetting industryhas been the industry's standard.</a></li>
    <li><svg width="5" height="7" viewBox="0 0 5 7"><path d="M1 1l2.5 2.5L1 6" fill="none" stroke="#2b2b2b" stroke-width="1.2"/></svg><a href="#">Dummy text ever since the 1500s, when an unknown printer.</a></li>
    <li><svg width="5" height="7" viewBox="0 0 5 7"><path d="M1 1l2.5 2.5L1 6" fill="none" stroke="#2b2b2b" stroke-width="1.2"/></svg><a href="#">Took a galley of type and scrambled it to make a type specimen book.</a></li>
    <li><svg width="5" height="7" viewBox="0 0 5 7"><path d="M1 1l2.5 2.5L1 6" fill="none" stroke="#2b2b2b" stroke-width="1.2"/></svg><a href="#">It has survived not only five centuries, but also the leap into electronic typesetting.</a></li>
    <li><svg width="5" height="7" viewBox="0 0 5 7"><path d="M1 1l2.5 2.5L1 6" fill="none" stroke="#2b2b2b" stroke-width="1.2"/></svg><a href="#">Remaining essentially unchanged.</a></li>
    <li><svg width="5" height="7" viewBox="0 0 5 7"><path d="M1 1l2.5 2.5L1 6" fill="none" stroke="#2b2b2b" stroke-width="1.2"/></svg><a href="#">Lorem Ipsum is simply dummy text of the printing.</a></li>
    <li><svg width="5" height="7" viewBox="0 0 5 7"><path d="M1 1l2.5 2.5L1 6" fill="none" stroke="#2b2b2b" stroke-width="1.2"/></svg><a href="#">Typesetting industryhas been the industry's standard.</a></li>
    <li><svg width="5" height="7" viewBox="0 0 5 7"><path d="M1 1l2.5 2.5L1 6" fill="none" stroke="#2b2b2b" stroke-width="1.2"/></svg><a href="#">Dummy text ever since the 1500s, when an unknown printer.</a></li>
    <li><svg width="5" height="7" viewBox="0 0 5 7"><path d="M1 1l2.5 2.5L1 6" fill="none" stroke="#2b2b2b" stroke-width="1.2"/></svg><a href="#">Took a galley of type and scrambled it to make a type specimen book.</a></li>
  </ul>
</main>

<aside class="info-card">
  <h3>Hours of Opration</h3>
  <p class="intro">Lorem Ipsum is simply dummy text of the printing and typesetting</p>
  <dl class="hours">
    <div><dt>Monday :</dt><dd>8:00 AM - 6:00 PM</dd></div>
    <div><dt>Tuesday :</dt><dd>8:00 AM - 6:00 PM</dd></div>
    <div><dt>Wednesday :</dt><dd>8:00 AM - 6:00 PM</dd></div>
    <div><dt>Thursday :</dt><dd>8:00 AM - 6:00 PM</dd></div>
    <div><dt>Friday :</dt><dd>8:00 AM - 6:00 PM</dd></div>
    <div><dt>Saturday :</dt><dd>9:00 AM - 4:00 PM</dd></div>
    <div><dt>Sunday :</dt><dd>9:00 AM - 4:00 PM</dd></div>
  </dl>
  <div class="rule"></div>
  <h4>CONTACT INFO</h4>
  <dl class="contact">
    <div><dt>Telephone :</dt><dd>604-555-0199</dd></div>
    <div><dt>Email:</dt><dd>contact@velmora.ca</dd></div>
    <div><dt>Address:</dt><dd>48 Alder Lane<br>Westmere,B.<br>Canada, V2X 9QR</dd></div>
  </dl>
</aside>

<footer class="footer">
  <a class="brand" href="#"><span class="dot"></span>Medical Clinics</a>
  <p class="about">Lorem Ipsum is simply dummy text of the printing and typesetting industry. Lorem Ipsum has been the industry's standard dummy text</p>
  <div class="footer-col" style="left:461px">
    <h5>Navigation</h5>
    <ul><li class="on">Home</li><li>Our Clinic</li><li>Newsletter</li><li>Our Staff</li><li>Resources</li></ul>
  </div>
  <div class="footer-col" style="left:686px">
    <h5>Links</h5>
    <ul><li>Help</li><li>Support</li><li>Privacy Policy</li></ul>
  </div>
  <div class="footer-col" style="left:836px;top:34px">
    <h5>Contact Us</h5>
    <dl class="footer-contact">
      <div><dt>Telephone :</dt><dd>604-555-0199</dd></div>
      <div><dt>Email:</dt><dd>contact@velmora.ca</dd></div>
      <div><dt>Address:</dt><dd>48 Alder Lane<br>Westmere,B. Canada,<br>V2X 9QR</dd></div>
    </dl>
  </div>
  <div class="bottom">
    <span style="left:162px">© 2015 Medical Clinces. All Rights Reservsd</span>
    <span style="left:462px">About Us</span>
    <span style="left:530px">Terms of Use</span>
    <span style="left:615px">Privacy Policy</span>
  </div>
</footer>

</body>
</html>
```